Mental Health care Company in Washington DC

We are a new mental health care services provider in Washington DC. Please look at these sites.
https://brightwaterfamilysupport.com
https://www.quietharborinc.com
https://willowgate-dc.org/
https://www.tidepathdc.com
https://www.thelanternofdc.com

```html
<!DOCTYPE html>
<html lang="en">
<head>
<meta charset="utf-8">
<title>Vela Health Services — Mental Health Care in Washington DC</title>
<link href="https://fonts.googleapis.com/css2?family=Poppins:wght@300;400;500;600;700&family=Caveat:wght@500&display=swap" rel="stylesheet">
<style>
:root{
  --orange:#F07D22;
  --orange-soft:#F6A45E;
  --orange-light:#F9B77A;
  --navy:#0F2147;
  --navy-2:#1B2E58;
  --teal:#4DB8C3;
  --teal-light:#A8D8DC;
  --mint:#EEF7F7;
  --text:#3B3F4A;
  --muted:#6C7180;
  --line:#D9DCE2;
  --white:#FFFFFF;
}
*{margin:0;padding:0;box-sizing:border-box}
html,body{width:1200px;height:4138px;overflow:hidden}
body{position:relative;background:var(--white);font-family:'Poppins',sans-serif;color:var(--text)}
.abs{position:absolute}
a{color:inherit;text-decoration:none}

/* top bar */
.topbar{left:0;top:0;width:1200px;height:35px;background:var(--orange-soft);font-size:11px;font-weight:500;color:var(--navy)}
.topbar .follow{left:141px;top:10px}
.topbar .social{top:9px;width:16px;height:16px;border-radius:50%;background:rgba(15,33,71,.75)}
.topbar .social.active{background:var(--white);border-radius:2px;top:0;height:35px;width:28px}
.topbar .contact{top:10px;display:flex;align-items:center;gap:6px}

/* header */
.header{left:0;top:35px;width:1200px;height:87px;background:var(--white)}
.brand{left:141px;top:20px;font-size:32px;font-weight:500;color:var(--navy);letter-spacing:-.5px;display:flex;align-items:center;gap:10px}
.brand .dot{width:12px;height:12px;border-radius:50%;background:var(--orange)}
.nav{top:35px;font-size:13px;font-weight:500;color:var(--navy)}
.btn-contact{left:917px;top:22px;width:142px;height:42px;border-radius:21px;background:var(--orange-soft);font-size:13px;font-weight:500;color:var(--navy);display:flex;align-items:center;padding-left:21px}
.arrow-ring{position:absolute;right:5px;top:5px;width:32px;height:32px;border-radius:50%;border:1.5px solid var(--navy);display:flex;align-items:center;justify-content:center}

/* hero */
.hero{left:0;top:122px;width:1200px;height:609px}
.hero-title{left:143px;top:118px;color:var(--white);font-size:35px;line-height:47px;font-weight:400}
.hero-title strong{font-weight:700;font-size:37px}
.hero-text{left:143px;top:270px;width:360px;color:var(--white);font-size:18px;line-height:26px;font-weight:300}
.btn-hero{left:143px;top:378px;width:216px;height:36px;border-radius:18px;background:var(--orange-soft);font-size:12.5px;font-weight:500;color:var(--navy);display:flex;align-items:center;padding-left:22px}
.btn-hero .arrow-ring{width:28px;height:28px;top:3px;right:4px}

/* features */
.feature{top:803px;width:300px}
.feature .icon{position:absolute;left:0;top:0;width:61px;height:61px;border-radius:50%;border:1px solid var(--line);display:flex;align-items:center;justify-content:center}
.feature h3{position:absolute;left:84px;top:3px;font-size:14px;font-weight:500;color:var(--navy);white-space:nowrap}
.feature p{position:absolute;left:84px;top:31px;width:210px;font-size:11.5px;line-height:19px;color:var(--muted)}
.divider{left:103px;top:952px;width:992px;height:2px;background:var(--line)}

/* question banner */
.question{left:141px;top:1025px;width:917px;height:207px;border-radius:20px;background:linear-gradient(90deg,#F07A1C 0%,#F59A49 55%,#F6C9A0 100%);overflow:hidden}
.question .photo{position:absolute;right:0;top:0;width:330px;height:207px;background:linear-gradient(90deg,rgba(246,201,160,0) 0%,#DCE7F1 45%,#C8D8E8 100%)}
.question .kicker{position:absolute;left:67px;top:38px;font-family:'Caveat',cursive;font-size:26px;color:#FDE3C6}
.question h2{position:absolute;left:67px;top:70px;width:540px;font-size:23px;line-height:34px;font-weight:500;color:var(--white)}
.question a{position:absolute;left:67px;top:146px;font-size:14px;font-weight:500;color:var(--white);text-decoration:underline}
.pills{left:1105px;top:1130px;width:95px;height:110px;background:linear-gradient(160deg,#CFE3EC,#E9B7C4)}

/* ticker */
.ticker{left:0;top:1317px;width:1200px;height:51px;background:var(--teal);color:var(--white);font-size:15px;font-weight:400;white-space:nowrap;display:flex;align-items:center}
.ticker .track{position:absolute;left:-26px;display:flex;align-items:center;gap:19px}
.ticker .item{display:flex;align-items:center;gap:19px}

/* about */
.about-bg{left:0;top:1368px;width:605px;height:567px;background:var(--mint);border-right:1px solid var(--line)}
.about-photo{left:0;top:1453px;width:519px;height:397px;border-radius:0 16px 16px 0;background:linear-gradient(135deg,#9FB7C7 0%,#D6C6B8 45%,#E9EDF0 70%,#B9CAD6 100%)}
.eyebrow{font-size:14px;font-weight:500;color:var(--teal);letter-spacing:.3px}
.about-eyebrow{left:673px;top:1459px;display:flex;align-items:center;gap:10px}
.about-eyebrow .rule{width:60px;height:1px;background:var(--line)}
.about-title{left:673px;top:1490px;font-size:30px;line-height:36px;font-weight:600;color:var(--navy)}
.about-text{left:673px;top:1578px;width:442px;font-size:12.6px;line-height:22.6px;color:var(--text)}
.btn-orange{border-radius:18px;background:var(--orange);color:var(--white);font-size:12.5px;font-weight:500;display:flex;align-items:center;justify-content:center}
.btn-about{left:673px;top:1810px;width:194px;height:36px}

/* services */
.center{left:0;width:1200px;text-align:center}
.services-eyebrow{top:2023px}
.spark-rule{left:560px;top:2052px;width:80px;height:10px}
.section-title{font-size:30px;font-weight:600;color:var(--navy);line-height:42px}
.services-title{top:2065px}
.service{top:2144px;width:282px;height:316px;border:1.5px solid #7A7F8C}
.service .photo{position:absolute;left:15px;top:14px;width:250px;height:142px}
.service h3{position:absolute;left:0;top:177px;width:100%;text-align:center;font-size:17px;font-weight:500;color:var(--navy)}
.service p{position:absolute;left:18px;top:218px;width:244px;text-align:center;font-size:12.3px;line-height:22.5px;color:var(--text)}
.service .badge{position:absolute;left:113px;top:288px;width:54px;height:54px;border-radius:50%;background:var(--teal);border:4px solid #DDF1F3;display:flex;align-items:center;justify-content:center}

/* wellness banner */
.wellness{left:0;top:2581px;width:1200px;height:401px;background:linear-gradient(90deg,#F5A15A 0%,#F39A4C 50%,#F07D22 100%)}
.wellness .photo{position:absolute;left:0;top:0;width:640px;height:401px;background:linear-gradient(90deg,#C8D3DD 0%,#E9DED3 40%,#F2C9A4 80%,rgba(245,161,90,0) 100%)}
.wellness h2{position:absolute;left:630px;top:90px;font-size:35px;line-height:48px;font-weight:600;color:var(--white)}
.wellness p{position:absolute;left:630px;top:204px;width:420px;font-size:13.5px;line-height:24px;color:#FFE7D2}
.btn-outline{position:absolute;left:631px;top:275px;width:245px;height:37px;border:1.5px solid #FFD7B6;border-radius:19px;color:var(--white);font-size:13px;font-weight:500;display:flex;align-items:center;justify-content:center}

/* values strip */
.values{top:3030px;font-size:77px;font-weight:600;line-height:100px;white-space:nowrap}
.values.outline{color:transparent;-webkit-text-stroke:1.3px #9AA0AB}
.values.solid{color:#111827}

/* testimonials */
.testimonials-title{top:3184px;font-size:31px;line-height:42px}
.review{top:3340px;width:283px;height:234px;background:var(--white);box-shadow:0 4px 18px rgba(15,33,71,.09)}
.review .quote{position:absolute;right:20px;top:-22px;width:38px;height:38px;border-radius:50%;background:var(--white);display:flex;align-items:center;justify-content:center;font-size:24px;font-weight:700;line-height:1}
.review .quote.teal{border:2px solid var(--teal);color:var(--teal)}
.review .quote.orange{border:2px solid var(--orange);color:var(--orange)}
.review .avatar{position:absolute;left:22px;top:-6px;width:58px;height:58px;border-radius:50%;background:linear-gradient(160deg,#C9CED6,#7E8794)}
.review .stars{position:absolute;left:104px;top:16px;display:flex;gap:4px}
.review h4{position:absolute;left:22px;top:72px;font-size:13.5px;font-weight:500;color:var(--navy)}
.review p{position:absolute;left:22px;top:97px;width:245px;font-size:11.6px;line-height:19.4px;color:var(--text)}
.dots{left:557px;top:3580px;display:flex;gap:8px}
.dots span{width:11px;height:11px;border-radius:50%;background:#D4D7DD}
.dots span.on{background:var(--orange)}

/* footer */
.footer{left:0;top:3671px;width:1200px;height:467px;background:var(--navy);color:#DDE3EE}
.footer .brand{left:139px;top:110px;color:var(--white);font-size:32px}
.footer .about-blurb{left:138px;top:184px;width:205px;font-size:12.3px;line-height:21.5px}
.footer h5{font-size:16.5px;font-weight:500;color:var(--orange)}
.footer ul{list-style:none;font-size:12.3px}
.footer ul li{height:32px}
.footer ul li::before{content:"•";color:var(--orange);margin-right:8px}
.footer .contact-block{left:527px;top:131px;width:230px;font-size:12.3px;line-height:21px}
.footer .contact-block .label{color:var(--orange)}
.stay{left:782px;top:85px;width:289px;height:254px;border-radius:12px;background:var(--navy-2)}
.stay h5{position:absolute;left:37px;top:42px}
.stay p{position:absolute;left:37px;top:78px;width:220px;font-size:12.3px;line-height:21.5px}
.stay .email{position:absolute;left:37px;top:130px;width:218px;height:37px;border-radius:19px;background:var(--white);color:#8A8F9A;font-size:12px;display:flex;align-items:center;padding-left:21px}
.stay .email svg{position:absolute;right:20px;top:12px}
.stay .subscribe{position:absolute;left:37px;top:186px;width:150px;height:37px;border-radius:19px;background:var(--orange);color:var(--white);font-size:13px;font-weight:500;display:flex;align-items:center;padding-left:22px}
.stay .subscribe svg{position:absolute;right:22px;top:12px}
.footer .rule{left:141px;top:408px;width:917px;height:1px;background:#33466E}
.footer .legal{top:430px;font-size:12.3px}
</style>
</head>
<body>

<svg width="0" height="0" style="position:absolute">
  <defs><path id="st" d="M7 1l1.8 3.8 4.2.5-3.1 2.9.8 4.1L7 10.3 3.3 12.3l.8-4.1L1 5.3l4.2-.5z"/></defs>
</svg>

<!-- Top bar -->
<div class="abs topbar">
  <span class="abs follow">Follow Us:</span>
  <span class="abs social active" style="left:208px"></span>
  <span class="abs social" style="left:214px;background:var(--navy)"></span>
  <span class="abs social" style="left:248px"></span>
  <span class="abs social" style="left:283px"></span>
  <span class="abs social" style="left:317px"></span>
  <span class="abs contact" style="left:780px">
    <svg width="14" height="14" viewBox="0 0 24 24" fill="var(--navy)"><path d="M6.6 10.8a15.1 15.1 0 0 0 6.6 6.6l2.2-2.2a1 1 0 0 1 1-.25 11.4 11.4 0 0 0 3.6.57 1 1 0 0 1 1 1V20a1 1 0 0 1-1 1A17 17 0 0 1 3 4a1 1 0 0 1 1-1h3.5a1 1 0 0 1 1 1c0 1.25.2 2.45.57 3.6a1 1 0 0 1-.25 1z"/></svg>
    202 555 0147
  </span>
  <span class="abs contact" style="left:916px">
    <svg width="15" height="12" viewBox="0 0 24 18" fill="var(--navy)"><path d="M0 0h24v18H0z"/><path d="M1 1l11 8 11-8" stroke="var(--orange-soft)" stroke-width="2" fill="none"/></svg>
    info@velahealth.com
  </span>
</div>

<!-- Header -->
<header class="abs header">
  <div class="abs brand"><span class="dot"></span>Vela Health</div>
  <a class="abs nav" style="left:527px">Home</a>
  <a class="abs nav" style="left:609px">About Us</a>
  <a class="abs nav" style="left:713px">Services</a>
  <a class="abs nav" style="left:810px">Our Team</a>
  <a class="abs btn-contact">Contact Us
    <span class="arrow-ring"><svg width="10" height="10" viewBox="0 0 10 10"><path d="M3 1l4 4-4 4" stroke="var(--navy)" stroke-width="1.5" fill="none"/></svg></span>
  </a>
</header>

<!-- Hero -->
<section class="abs hero">
  <svg class="abs" style="left:0;top:0" width="1200" height="609" viewBox="0 0 1200 609">
    <defs>
      <linearGradient id="heroPhoto" x1="0" y1="0" x2="1" y2="1">
        <stop offset="0" stop-color="#F3D59A"/>
        <stop offset=".45" stop-color="#D9B37A"/>
        <stop offset=".8" stop-color="#A89A58"/>
        <stop offset="1" stop-color="#7E8A4A"/>
      </linearGradient>
    </defs>
    <path d="M540 0H1200V350C1080 420 900 500 720 609H680Z" fill="var(--teal-light)"/>
    <path d="M0 0H600C650 250 620 470 690 609C590 560 470 470 300 478C170 486 90 532 0 508Z" fill="var(--navy)"/>
    <circle cx="789" cy="292" r="252" fill="url(#heroPhoto)" role="img" aria-label="Photo of a woman breathing freely in a sunlit grass field"/>
  </svg>
  <h1 class="abs hero-title">Compassionate<br><strong>Mental Health Care</strong><br>in Washington DC</h1>
  <p class="abs hero-text">Your journey to wellness begins with understanding. We're here to guide you every step of the way.</p>
  <a class="abs btn-hero">Schedule Consultation
    <span class="arrow-ring"><svg width="10" height="10" viewBox="0 0 10 10"><path d="M3 1l4 4-4 4" stroke="var(--navy)" stroke-width="1.5" fill="none"/></svg></span>
  </a>
</section>

<!-- Features -->
<div class="abs feature" style="left:141px">
  <div class="icon"><svg width="28" height="28" viewBox="0 0 24 24" fill="none" stroke="var(--orange)" stroke-width="1.4"><path d="M12 11s-4-2.6-4-5a2 2 0 0 1 4-.6A2 2 0 0 1 16 6c0 2.4-4 5-4 5z"/><path d="M3 15h5l3 2h5a1.5 1.5 0 0 1 0 3H9M3 20h4"/></svg></div>
  <h3>Personalized Family Care</h3>
  <p>We treat you like family, building lasting relationships based on trust and compassion</p>
</div>
<div class="abs feature" style="left:451px">
  <div class="icon"><svg width="28" height="28" viewBox="0 0 24 24" fill="none" stroke="var(--teal)" stroke-width="1.4"><path d="M12 20S3 14.5 3 8.5A4.5 4.5 0 0 1 12 6a4.5 4.5 0 0 1 9 2.5C21 14.5 12 20 12 20z"/><path d="M12 9.5v5M9.5 12h5"/></svg></div>
  <h3>Comprehensive Services</h3>
  <p>From routine checkups to specialized testing, we offer a wide range of services to meet your needs</p>
</div>
<div class="abs feature" style="left:769px">
  <div class="icon"><svg width="28" height="28" viewBox="0 0 24 24" fill="none" stroke="var(--orange)" stroke-width="1.4"><circle cx="12" cy="10" r="7"/><circle cx="12" cy="10" r="4"/><path d="M8 16l-2 6 6-2 6 2-2-6"/></svg></div>
  <h3>Experienced &amp; Caring Staff</h3>
  <p>Our team of dedicated professionals is committed to providing the highest quality care</p>
</div>
<div class="abs divider"></div>

<!-- Question banner -->
<section class="abs question">
  <div class="photo" role="img" aria-label="Photo of a doctor holding a stethoscope"></div>
  <span class="kicker">Have A Question?</span>
  <h2>Reach out to schedule your appointment or get answers to your questions</h2>
  <a>Schedule an Appointment Today!</a>
</section>
<div class="abs pills" role="img" aria-label="Photo of scattered pills and a syringe"></div>

<!-- Ticker -->
<div class="abs ticker">
  <div class="track">
    <span>te Care</span>
    <span class="item"><svg width="20" height="18" viewBox="0 0 24 22" fill="none" stroke="#fff" stroke-width="2"><path d="M12 20S2 14 2 7.5A5 5 0 0 1 12 5a5 5 0 0 1 10 2.5C22 14 12 20 12 20z"/></svg>Family-Focused</span>
    <span class="item"><svg width="20" height="18" viewBox="0 0 24 22" fill="none" stroke="#fff" stroke-width="2"><path d="M12 20S2 14 2 7.5A5 5 0 0 1 12 5a5 5 0 0 1 10 2.5C22 14 12 20 12 20z"/></svg>Comprehensive Services</span>
    <span class="item"><svg width="20" height="18" viewBox="0 0 24 22" fill="none" stroke="#fff" stroke-width="2"><path d="M12 20S2 14 2 7.5A5 5 0 0 1 12 5a5 5 0 0 1 10 2.5C22 14 12 20 12 20z"/></svg>Advanced Testing</span>
    <span class="item"><svg width="20" height="18" viewBox="0 0 24 22" fill="none" stroke="#fff" stroke-width="2"><path d="M12 20S2 14 2 7.5A5 5 0 0 1 12 5a5 5 0 0 1 10 2.5C22 14 12 20 12 20z"/></svg>Community Health</span>
    <span class="item"><svg width="20" height="18" viewBox="0 0 24 22" fill="none" stroke="#fff" stroke-width="2"><path d="M12 20S2 14 2 7.5A5 5 0 0 1 12 5a5 5 0 0 1 10 2.5C22 14 12 20 12 20z"/></svg>Personalized Healthcare</span>
    <span class="item"><svg width="20" height="18" viewBox="0 0 24 22" fill="none" stroke="#fff" stroke-width="2"><path d="M12 20S2 14 2 7.5A5 5 0 0 1 12 5a5 5 0 0 1 10 2.5C22 14 12 20 12 20z"/></svg>Comprehensive Services</span>
  </div>
</div>

<!-- About -->
<div class="abs about-bg"></div>
<div class="abs about-photo" role="img" aria-label="Photo of a nurse giving a high five to a boy held by his father"></div>
<div class="abs eyebrow about-eyebrow">WHO WE ARE
  <svg width="18" height="18" viewBox="0 0 18 18"><path d="M9 1v6M9 11v6" stroke="var(--orange)" stroke-width="2"/><path d="M1 9h6M11 9h6" stroke="var(--teal)" stroke-width="2"/></svg>
  <span class="rule"></span>
</div>
<h2 class="abs about-title">A Trusted Mental Health<br>Partner In DC</h2>
<p class="abs about-text">Lorem Ipsum is simply dummy text of the printing and typesetting industry. Lorem Ipsum has been the industry's standard dummy text ever since the 1500s, when an unknown printer took a galley of type and scrambled it to make a type specimen book. It has survived not only five centuries, but also the leap into electronic typesetting, remaining essentially unchanged. It was popularised in the 1960s with the release of Lettersheet sheets containing Lorem Ipsum passages, and more recently with desktop publishing software like PageComposer including versions of Lorem Ipsum</p>
<a class="abs btn-orange btn-about">Learn More About Us</a>

<!-- Services -->
<div class="abs center eyebrow services-eyebrow">OUR CORE SERVICES</div>
<svg class="abs spark-rule" viewBox="0 0 80 10"><path d="M0 5h32M48 5h32" stroke="var(--line)"/><path d="M40 0v4M40 6v4" stroke="var(--orange)" stroke-width="2"/><path d="M35 5h4M41 5h4" stroke="var(--teal)" stroke-width="2"/></svg>
<h2 class="abs center section-title services-title">Transformative Services For Real Results</h2>

<article class="abs service" style="left:141px">
  <div class="photo" role="img" aria-label="Photo of a therapist listening to a young woman on a sofa" style="background:linear-gradient(120deg,#CFC6BD,#E8E3DC 50%,#B89C8E)"></div>
  <h3>Individual Therapy</h3>
  <p>Lorem Ipsum is simply dummy text of the printing and typesetting industry. Lorem Ipsum has been the.</p>
  <span class="badge"><svg width="24" height="24" viewBox="0 0 24 24" fill="none" stroke="#fff" stroke-width="1.6"><path d="M9 20v-3a6 6 0 1 1 8-5.6L18.5 14H17v3h-3v3z"/><circle cx="12" cy="10" r="2"/></svg></span>
</article>
<article class="abs service" style="left:459px">
  <div class="photo" role="img" aria-label="Photo of a group of doctors in white coats" style="background:linear-gradient(120deg,#6F7A86,#D7DCE1 50%,#55606C)"></div>
  <h3>Support Groups</h3>
  <p>Lorem Ipsum is simply dummy text of the printing and typesetting industry. Lorem Ipsum has been the.</p>
  <span class="badge"><svg width="24" height="24" viewBox="0 0 24 24" fill="none" stroke="#fff" stroke-width="1.6"><circle cx="8" cy="8" r="2.5"/><circle cx="16" cy="8" r="2.5"/><path d="M3 18a5 5 0 0 1 10 0M11 18a5 5 0 0 1 10 0"/></svg></span>
</article>
<article class="abs service" style="left:777px">
  <div class="photo" role="img" aria-label="Photo of a counselor speaking with an older patient" style="background:linear-gradient(120deg,#2E4C6E,#9EB8CC 50%,#43617E)"></div>
  <h3>Counseling</h3>
  <p>Lorem Ipsum is simply dummy text of the printing and typesetting industry. Lorem Ipsum has been the.</p>
  <span class="badge"><svg width="24" height="24" viewBox="0 0 24 24" fill="none" stroke="#fff" stroke-width="1.6"><path d="M4 4h16v12H9l-5 4z"/><path d="M8 8h8M8 12h6"/></svg></span>
</article>

<!-- Wellness banner -->
<section class="abs wellness">
  <div class="photo" role="img" aria-label="Photo of a doctor with a clipboard consulting a smiling young woman"></div>
  <h2>Ready To Begin<br>Your Journey To Wellness?</h2>
  <p>Get started on the path to health through the quality medical care our team provides!</p>
  <a class="btn-outline">Schedule Your Appointment</a>
</section>

<!-- Values -->
<div class="abs values outline" style="right:832px">Trustworthy_</div>
<div class="abs values solid" style="left:383px">Caring_</div>
<div class="abs values outline" style="left:719px">Professional</div>

<!-- Testimonials -->
<h2 class="abs center section-title testimonials-title">What Our Clients Are Saying – Real Success Stories<br>from Trusted Partners</h2>

<article class="abs review" style="left:-158px">
  <span class="quote teal">”</span>
  <span class="avatar" role="img" aria-label="Client portrait"></span>
  <div class="stars"><svg width="80" height="14" viewBox="0 0 80 14"><g fill="var(--orange)"><use href="#st" x="0"/><use href="#st" x="16"/><use href="#st" x="32"/></g><g fill="none" stroke="var(--orange)"><use href="#st" x="48"/><use href="#st" x="64"/></g></svg></div>
  <h4>Leah Marsh</h4>
  <p>Lorem Ipsum is simply dummy text of the printing and typesetting industry. Lorem Ipsum has been the industry's standard dummy text ever since the 1500s, when an unknown printer took a galley of type.</p>
</article>
<article class="abs review" style="left:151px">
  <span class="quote orange">”</span>
  <span class="avatar" role="img" aria-label="Client portrait"></span>
  <div class="stars"><svg width="80" height="14" viewBox="0 0 80 14"><g fill="var(--orange)"><use href="#st" x="0"/><use href="#st" x="16"/><use href="#st" x="32"/></g><g fill="none" stroke="var(--orange)"><use href="#st" x="48"/><use href="#st" x="64"/></g></svg></div>
  <h4>Owen Marlo</h4>
  <p>Lorem Ipsum is simply dummy text of the printing and typesetting industry. Lorem Ipsum has been the industry's standard dummy text ever since the 1500s.</p>
</article>
<article class="abs review" style="left:459px;height:180px">
  <span class="quote teal">”</span>
  <span class="avatar" role="img" aria-label="Client portrait"></span>
  <div class="stars"><svg width="80" height="14" viewBox="0 0 80 14"><g fill="var(--orange)"><use href="#st" x="0"/><use href="#st" x="16"/><use href="#st" x="32"/></g><g fill="none" stroke="var(--orange)"><use href="#st" x="48"/><use href="#st" x="64"/></g></svg></div>
  <h4>Rafe Linden</h4>
  <p>Lorem Ipsum is simply dummy text of the printing and typesetting industry. Lorem Ipsum has been the industry's.</p>
</article>
<article class="abs review" style="left:766px">
  <span class="quote orange">”</span>
  <span class="avatar" role="img" aria-label="Client portrait"></span>
  <div class="stars"><svg width="80" height="14" viewBox="0 0 80 14"><g fill="var(--orange)"><use href="#st" x="0"/><use href="#st" x="16"/><use href="#st" x="32"/></g><g fill="none" stroke="var(--orange)"><use href="#st" x="48"/><use href="#st" x="64"/></g></svg></div>
  <h4>Nora Castell</h4>
  <p>Lorem Ipsum is simply dummy text of the printing and typesetting industry. Lorem Ipsum has been the industry's standard dummy text ever since the 1500s, when an unknown printer took a galley of type.</p>
</article>
<article class="abs review" style="left:1073px">
  <span class="quote teal">”</span>
  <span class="avatar" role="img" aria-label="Client portrait"></span>
  <div class="stars"><svg width="80" height="14" viewBox="0 0 80 14"><g fill="var(--orange)"><use href="#st" x="0"/><use href="#st" x="16"/><use href="#st" x="32"/></g><g fill="none" stroke="var(--orange)"><use href="#st" x="48"/><use href="#st" x="64"/></g></svg></div>
  <h4>Ivy Renholt</h4>
  <p>Lorem Ipsum is simply dummy text of the printing and typesetting industry. Lorem Ipsum has been the industry's standard dummy text ever.</p>
</article>
<div class="abs dots"><span class="on"></span><span></span><span></span><span></span><span></span></div>

<!-- Footer -->
<footer class="abs footer">
  <div class="abs brand"><span class="dot"></span>Vela Health</div>
  <p class="abs about-blurb">Committed to providing expert mental health care in Washington DC, we empower individuals to heal, grow, and thrive</p>

  <h5 class="abs" style="left:368px;top:93px">Quick Links</h5>
  <ul class="abs" style="left:368px;top:136px">
    <li>Home</li><li>About Us</li><li>Sevices</li><li>Blog</li><li>FAQs</li><li>Contact Us</li>
  </ul>

  <h5 class="abs" style="left:527px;top:93px">Contact Info</h5>
  <div class="abs contact-block">
    <p>2210 Alder Lane Suite 4, Brookmere, Maryland 20914, United States</p>
    <p class="label" style="margin-top:14px">Email Address :</p>
    <p>info@VelaMentalHealth.com</p>
    <p class="label" style="margin-top:14px">Phone Number :</p>
    <p>(202)-555-0147</p>
  </div>

  <div class="abs stay">
    <h5>Stay in Touch</h5>
    <p>Stay updated with health tips and exclusive offers!</p>
    <div class="email">Email address
      <svg width="15" height="12" viewBox="0 0 24 18"><rect width="24" height="18" fill="#8A8F9A"/><path d="M1 1l11 8 11-8" stroke="#fff" stroke-width="2" fill="none"/></svg>
    </div>
    <a class="subscribe">Subscribe
      <svg width="14" height="14" viewBox="0 0 24 24" fill="#fff"><path d="M2 2l20 10L2 22l4-10z"/></svg>
    </a>
  </div>

  <div class="abs rule"></div>
  <p class="abs legal" style="left:141px">Copyright © 2025 Vela Mental Health | All Rights Reserved.</p>
  <p class="abs legal" style="right:142px">Terms &amp; Condition &nbsp;|&nbsp; Privacy Policy &nbsp;|&nbsp; Support</p>
</footer>

</body>
</html>
```